Business Card Design

WE are looking for a premium quality Business Cards for a Law Firm . Copies of our current business card is attached.

Contact Information for Business Card

xyz

```html
<!DOCTYPE html>
<html lang="en">
<head>
<meta charset="utf-8">
<title>Harcourt Lawyers – Business Card</title>
<link rel="stylesheet" href="https://fonts.googleapis.com/css2?family=Libre+Baskerville:wght@400;700&display=swap">
<style>
  :root{
    --bg:#2a2e35;
    --card-front:#ffffff;
    --card-back:#f4f4f4;
    --green:#12301f;
    --gold:#c4a256;
    --gold-pale:#ece4d3;
    --ink:#111111;
  }
  *{margin:0;padding:0;box-sizing:border-box}
  html,body{width:1200px;height:780px;overflow:hidden}
  body{background:var(--bg);font-family:"Libre Baskerville",Georgia,serif;position:relative}
  .card{position:absolute;top:225px;width:540px;height:330px;overflow:hidden;box-shadow:0 10px 30px rgba(0,0,0,.35)}
  .card--back{left:40px;background:var(--card-back)}
  .card--front{left:620px;background:var(--card-front)}

  .brand{display:flex;align-items:center;gap:12px;color:var(--green);font-weight:700}
  .brand__mark{width:34px;height:34px;border:3px solid var(--gold);border-radius:50%;flex:none}
  .brand__name{font-size:19px;letter-spacing:.5px;line-height:1.1;white-space:nowrap}

  .card--front .brand{position:absolute;left:50%;top:50%;transform:translate(-50%,-50%);gap:18px}
  .card--front .brand__mark{width:62px;height:62px;border-width:4px}
  .card--front .brand__name{font-size:30px}

  .card--back .brand{position:absolute;left:28px;top:26px}

  .address{position:absolute;left:28px;top:84px;font-size:12px;font-weight:700;font-style:normal;line-height:1.55;color:var(--ink)}
  .contacts{position:absolute;left:28px;top:150px;list-style:none;font-size:12px;font-weight:700;color:var(--ink)}
  .contacts li{display:flex;align-items:center;gap:9px;line-height:1.7;white-space:nowrap}
  .contacts svg{width:13px;height:13px;flex:none}

  .watermark-ring{position:absolute;left:250px;top:110px;width:330px;height:330px;border:16px solid var(--gold-pale);border-radius:50%}
  .gold-band{position:absolute;right:0;top:200px;width:40px;height:130px;background:var(--gold)}

  .person{position:absolute;right:58px;top:242px;text-align:right;white-space:nowrap}
  .person__name{font-size:26px;font-weight:700;color:var(--gold);letter-spacing:1px;line-height:1.3;text-transform:uppercase}
  .person__role,.person__degrees{font-size:12px;font-weight:700;color:var(--ink);line-height:1.6}
</style>
</head>
<body>
  <section class="card card--back" aria-label="Business card, contact side">
    <div class="watermark-ring"></div>
    <div class="gold-band"></div>

    <div class="brand">
      <span class="brand__mark"></span>
      <span class="brand__name">HARCOURT LAWYERS</span>
    </div>

    <address class="address">
      Level 3, Harcourt House,<br>
      88 Elmwood Terrace,<br>
      Elmwood, QLD 4000
    </address>

    <ul class="contacts">
      <li>
        <svg viewBox="0 0 24 24" fill="var(--gold)"><path d="M6.6 10.8a15 15 0 0 0 6.6 6.6l2.2-2.2a1 1 0 0 1 1-.25 11.4 11.4 0 0 0 3.6.57 1 1 0 0 1 1 1V20a1 1 0 0 1-1 1A17 17 0 0 1 3 4a1 1 0 0 1 1-1h3.5a1 1 0 0 1 1 1c0 1.25.2 2.450.57 3.57a1 1 0 0 1-.25 1z"/></svg>
        +61 7 3000 4812
      </li>
      <li>
        <svg viewBox="0 0 24 24" fill="none" stroke="var(--gold)" stroke-width="2"><rect x="6" y="2" width="12" height="20" rx="2"/><line x1="11" y1="18" x2="13" y2="18"/></svg>
        +61 0400 217 396
      </li>
      <li>
        <svg viewBox="0 0 24 24" fill="none" stroke="var(--gold)" stroke-width="2"><circle cx="12" cy="12" r="10"/><ellipse cx="12" cy="12" rx="4" ry="10"/><line x1="2" y1="12" x2="22" y2="12"/></svg>
        www.harcourtlawyers.com.au
      </li>
      <li>
        <svg viewBox="0 0 24 24" fill="none" stroke="var(--gold)" stroke-width="2"><rect x="2" y="5" width="20" height="14" rx="2"/><polyline points="2,6 12,13 22,6"/></svg>
        daniel@harcourtlawyers.com.au
      </li>
    </ul>

    <div class="person">
      <p class="person__name">Daniel Rourke</p>
      <p class="person__role">Director and Principal Solicitor</p>
      <p class="person__degrees">MBA, Juris Doctor</p>
    </div>
  </section>

  <section class="card card--front" aria-label="Business card, brand side">
    <div class="brand">
      <span class="brand__mark"></span>
      <span class="brand__name">HARCOURT LAWYERS</span>
    </div>
  </section>
</body>
</html>
```